Website design for lighting products company

We want a design for our website. The website is for a company that sells lighting products. The structure is similar to the below website. We really like their design as well: www.palvenorlighting.com

Industry/Entity Type

Lighting

Number of Pages Required

5+ page

Colors

Designer to choose colors to be used in the design.

Requirements
Must have
• Simple design

```html
<!DOCTYPE html>
<html lang="en">
<head>
<meta charset="utf-8">
<title>Palvenor Lighting</title>
<link href="https://fonts.googleapis.com/css2?family=Montserrat:wght@300;400;500;600;700&display=swap" rel="stylesheet">
<style>
:root{
  --yellow:#f2b705;
  --dark:#2b2b2b;
  --text:#444;
  --muted:#8a8a8a;
  --line:#e4e4e4;
  --soft:#f4f4f4;
  --white:#fff;
}
*{box-sizing:border-box;margin:0;padding:0}
html,body{width:1200px;height:2276px;overflow:hidden}
body{font-family:'Montserrat',sans-serif;color:var(--text);background:var(--white);position:relative}
.abs{position:absolute}

/* header */
.topbar{left:640px;top:0;width:560px;height:30px;background:var(--dark);color:#ddd;font-size:12px;display:flex;align-items:center;gap:22px;padding-left:54px}
.topbar .phone{display:flex;align-items:center;gap:6px}
.topbar svg{fill:var(--yellow)}
.brand{left:44px;top:26px;display:flex;align-items:center;gap:12px}
.brand .dot{width:34px;height:34px;border-radius:50%;background:var(--yellow)}
.brand .name{font-size:26px;font-weight:700;color:var(--dark);letter-spacing:.5px}
.nav{left:474px;top:66px;display:flex;gap:50px;font-size:15px;color:var(--dark)}
.nav a{color:inherit;text-decoration:none;padding-bottom:8px}
.nav a.active{color:var(--yellow);border-bottom:2px solid var(--yellow)}

/* hero */
.hero{left:0;top:120px;width:1200px;height:580px;background:linear-gradient(110deg,#6b5a49 0%,#c9b8a3 30%,#e8e1d6 55%,#9c958c 80%,#5d5a57 100%)}
.hero-shade{left:0;top:120px}
.hero-title{left:786px;top:410px;font-size:40px;font-weight:500;color:var(--white)}
.hero-sub{left:786px;top:468px;width:330px;font-size:12px;line-height:18px;color:#eee}
.btn{background:var(--yellow);color:var(--white);font-size:11px;font-weight:600;text-transform:uppercase;letter-spacing:.5px;display:flex;align-items:center;justify-content:center}
.hero-btn{left:924px;top:524px;width:110px;height:34px}
.arrow{color:var(--white);font-size:44px;font-weight:300}

/* bulbs */
.bulbs{left:490px;top:700px;width:220px;height:100px;background:linear-gradient(180deg,#f6f6f6,#fbf4dd)}

/* about */
.about-title{left:178px;top:848px;font-size:34px;font-weight:400;color:var(--dark)}
.about-rule{left:178px;top:896px;width:70px;height:2px;background:var(--yellow)}
.about-text{left:178px;top:914px;width:380px;font-size:12px;line-height:21px;color:var(--muted)}
.about-btn{left:178px;top:1108px;width:110px;height:34px}
.photo{background:linear-gradient(135deg,#dfe2e4,#9fa6ab)}
.p1{left:598px;top:852px;width:208px;height:148px}
.p2{left:812px;top:852px;width:210px;height:148px;background:linear-gradient(135deg,#e7e7e7,#b8b4ad)}
.p3{left:598px;top:1006px;width:424px;height:152px;background:linear-gradient(135deg,#cfd6dc,#8c959c)}

/* products */
.products{left:0;top:1250px;width:1200px;height:640px;background:var(--soft)}
.section-title{left:0;top:1290px;width:1200px;text-align:center;font-size:34px;color:var(--dark)}
.card{top:1400px;width:206px;height:266px;background:var(--white);border:1px solid var(--line)}
.card.active{border:2px solid var(--yellow)}
.card .img{position:absolute;left:28px;top:26px;width:150px;height:150px}
.card p{position:absolute;left:16px;right:16px;top:190px;text-align:center;font-size:12px;line-height:18px;color:var(--muted)}
.prod-btn{left:650px;top:1678px;width:110px;height:34px}
.p-arrow{color:#bbb;font-size:44px;font-weight:300;top:1500px}

/* subscribe */
.sub-title{left:128px;top:1956px;font-size:24px;color:var(--dark)}
.sub-input{left:706px;top:1950px;width:210px;height:38px;border:1px solid #ccc;font-size:11px;color:#999;padding:12px 14px}
.sub-btn{left:916px;top:1950px;width:106px;height:38px}

/* footer */
.footer{left:0;top:2030px;width:1200px;height:216px;background:var(--soft)}
.foot-brand{left:176px;top:2104px}
.col{top:2058px;font-size:11px;line-height:18px;color:var(--muted)}
.col h4{font-size:14px;font-weight:500;color:var(--dark);margin-bottom:16px}
.col li{list-style:none}
.contact-row{display:flex;gap:10px;align-items:flex-start;margin-bottom:10px}
.contact-row svg{flex:none;margin-top:3px;fill:var(--yellow)}
.social{left:1010px;top:2196px;display:flex;gap:8px}
.social span{width:22px;height:22px;border-radius:50%;background:#555}
.social span.hi{background:var(--yellow)}
.bottom{left:0;top:2246px;width:1200px;height:30px;background:var(--white);font-size:10px;color:var(--muted);padding:9px 130px}
.bottom-bar{left:0;top:2266px;width:420px;height:10px;background:var(--yellow)}
</style>
</head>
<body>

<header>
  <div class="abs topbar">
    <span class="phone"><svg width="12" height="12" viewBox="0 0 24 24"><path d="M6.6 10.8a15 15 0 006.6 6.6l2.2-2.2c.3-.3.7-.4 1-.2 1.1.4 2.3.6 3.6.6.6 0 1 .4 1 1V20c0 .6-.4 1-1 1A17 17 0 013 4c0-.6.4-1 1-1h3.5c.6 0 1 .4 1 1 0 1.3.2 2.5.6 3.6.1.3 0 .7-.2 1z"/></svg>(Phone) 555 018 2740</span>
    <svg width="13" height="13" viewBox="0 0 24 24"><circle cx="10" cy="10" r="7" fill="none" stroke="#f2b705" stroke-width="2.5"/><path d="M15 15l6 6" stroke="#f2b705" stroke-width="2.5"/></svg>
    <svg width="14" height="13" viewBox="0 0 24 24"><path d="M3 4h3l3 11h10l2-8H8" fill="none" stroke="#f2b705" stroke-width="2"/><circle cx="10" cy="19" r="1.8"/><circle cx="18" cy="19" r="1.8"/></svg>
  </div>
  <div class="abs brand"><span class="dot"></span><span class="name">Palvenor Lighting</span></div>
  <nav class="abs nav">
    <a class="active">Home</a><a>Products</a><a>Solutions</a><a>About</a><a>News</a><a>Contact</a>
  </nav>
</header>

<section>
  <div class="abs hero" role="img" aria-label="Photo of glass pendant lamps with glowing filament bulbs"></div>
  <svg class="abs hero-shade" width="1200" height="580"><polygon points="860,0 1200,0 1200,580 640,580" fill="#2b2b2b" opacity=".55"/></svg>
  <span class="abs arrow" style="left:24px;top:380px">‹</span>
  <span class="abs arrow" style="left:1160px;top:380px">›</span>
  <h1 class="abs hero-title">Palvenor Lighting</h1>
  <p class="abs hero-sub">Warm light for homes, offices and modern retail spaces everywhere.</p>
  <div class="abs btn hero-btn">Read more</div>
</section>

<div class="abs bulbs" role="img" aria-label="Illustration of hanging light bulbs"></div>

<section>
  <h2 class="abs about-title">About Palvenor Lighting</h2>
  <div class="abs about-rule"></div>
  <p class="abs about-text">We design and supply energy efficient lighting for homes, offices, hotels and retail spaces. Our team works closely with architects and contractors to choose fittings that suit each room, from soft ambient pendants to bright commercial panels. Every product is tested for long life, low running cost and easy installation. We hold stock of more than two thousand items and deliver across the region within days. Talk to us about your next project.</p>
  <div class="abs btn about-btn">Read more</div>
  <div class="abs photo p1" role="img" aria-label="Photo of a bright modern kitchen interior"></div>
  <div class="abs photo p2" role="img" aria-label="Photo of an open office with ceiling lights"></div>
  <div class="abs photo p3" role="img" aria-label="Photo of a commercial lobby with panel lighting"></div>
</section>

<section>
  <div class="abs products"></div>
  <h2 class="abs section-title">Our Products</h2>
  <span class="abs p-arrow" style="left:98px">‹</span>
  <span class="abs p-arrow" style="left:1084px">›</span>
  <div class="abs card" style="left:168px"><div class="img" role="img" aria-label="Square LED panel" style="background:linear-gradient(135deg,#fafafa,#e2e2e2)"></div><p>Slim square<br>LED panel</p></div>
  <div class="abs card" style="left:388px"><div class="img" role="img" aria-label="Linear batten light" style="background:linear-gradient(135deg,#f7f7f7,#d9d9d9)"></div><p>Linear batten<br>tube light</p></div>
  <div class="abs card active" style="left:602px"><div class="img" role="img" aria-label="Candle LED bulb" style="background:radial-gradient(circle,#fbfbfb,#e4e4e4)"></div><p>Warm candle<br>LED bulb</p></div>
  <div class="abs card" style="left:822px"><div class="img" role="img" aria-label="Square surface downlight" style="background:linear-gradient(135deg,#fafafa,#dedede)"></div><p>Square surface<br>downlight</p></div>
  <div class="abs btn prod-btn">Read more</div>
</section>

<section>
  <h3 class="abs sub-title">Subscribe to news and updates</h3>
  <div class="abs sub-input">Email Address</div>
  <div class="abs btn sub-btn">Subscribe</div>
</section>

<footer>
  <div class="abs footer"></div>
  <div class="abs brand foot-brand"><span class="dot"></span><span class="name">Palvenor Lighting</span></div>
  <div class="abs col" style="left:474px;width:200px">
    <h4>Contact</h4>
    <div class="contact-row"><svg width="10" height="12" viewBox="0 0 24 24"><path d="M12 2a7 7 0 00-7 7c0 5 7 13 7 13s7-8 7-13a7 7 0 00-7-7z"/></svg><span>27 Harbour Road, Unit 4<br>Ashford 4021</span></div>
    <div class="contact-row"><svg width="10" height="12" viewBox="0 0 24 24"><path d="M6.6 10.8a15 15 0 006.6 6.6l2.2-2.2c.3-.3.7-.4 1-.2 1.1.4 2.3.6 3.6.6.6 0 1 .4 1 1V20c0 .6-.4 1-1 1A17 17 0 013 4c0-.6.4-1 1-1h3.5c.6 0 1 .4 1 1 0 1.3.2 2.5.6 3.6.1.3 0 .7-.2 1z"/></svg><span>(02) 5550 1827<br>(02) 5550 1828</span></div>
    <div class="contact-row"><svg width="12" height="10" viewBox="0 0 24 18"><rect x="1" y="1" width="22" height="16" fill="none" stroke="#f2b705" stroke-width="2"/><path d="M1 1l11 9 11-9" fill="none" stroke="#f2b705" stroke-width="2"/></svg><span>info@palvenorlighting.com<br>www.palvenorlighting.com</span></div>
  </div>
  <div class="abs col" style="left:730px">
    <h4>Company</h4>
    <ul><li>About us</li><li>Our projects</li><li>Careers</li><li>News and events</li><li>Contact us</li><li>Privacy policy</li></ul>
  </div>
  <div class="abs col" style="left:912px">
    <h4>Products</h4>
    <ul><li>Pendant lights</li><li>LED panels</li><li>Downlights</li><li>Tube lights</li><li>Smart bulbs</li><li>Outdoor lights</li></ul>
  </div>
  <div class="abs social"><span></span><span></span><span></span><span class="hi"></span></div>
  <div class="abs bottom">© 2024 Palvenor Lighting. All rights reserved.</div>
  <div class="abs bottom-bar"></div>
</footer>

</body>
</html>
```